Looking for a modern, Professional business card design

We have a simple business card, but are looking for a more modern, professional look. A sample of the basic card is attached as well as the logo. We would also like to add that we offer:
Struggling with your finances?
- Learn to become debt free
- Discover the power of cash
- Control your money instead of it controlling you
Let us help you achieve a new level of financial freedom!
Also, we would like to have a "SPECIAL OFFER!: FREE 30 minute consultation"
Financial Planning

```html
<!DOCTYPE html>
<html lang="en">
<head>
<meta charset="utf-8">
<title>Summit Money Coaching – Business Card</title>
<link href="https://fonts.googleapis.com/css2?family=Open+Sans:ital,wght@0,400;0,600;0,700;0,800;1,400&display=swap" rel="stylesheet">
<style>
  :root {
    --stage: #ecebe7;
    --green-dark: #2f7f2c;
    --green-mid: #4a9e34;
    --green-light: #8cc63f;
    --brand-green: #5aa832;
    --ink: #1f1f1f;
    --ink-soft: #444444;
    --white: #ffffff;
    --tint: #e9f4dd;
  }
  * { box-sizing: border-box; margin: 0; padding: 0; }
  html, body { width: 1200px; height: 843px; overflow: hidden; }
  body {
    background: var(--stage);
    font-family: "Open Sans", Arial, sans-serif;
    position: relative;
  }
  .card {
    position: absolute;
    top: 266px;
    width: 540px;
    height: 310px;
    border-radius: 18px;
    overflow: hidden;
    box-shadow: 0 10px 24px rgba(0,0,0,.18);
  }

  /* Back side */
  .card-back {
    left: 40px;
    background: radial-gradient(ellipse at 58% 30%, var(--green-light) 0%, var(--green-mid) 40%, var(--green-dark) 100%);
    color: var(--white);
  }
  .card-back .brand {
    position: absolute; right: 30px; top: 26px; text-align: right;
  }
  .card-back .brand-name {
    font-weight: 800; font-size: 44px; letter-spacing: 2px; line-height: 1;
  }
  .card-back .brand-sub {
    font-weight: 800; font-size: 17px; letter-spacing: 1px; margin-top: 2px;
  }
  .card-back .brand-tag {
    font-style: italic; font-size: 10px; opacity: .85; margin-top: 2px;
  }
  .pitch { position: absolute; left: 30px; top: 132px; right: 24px; }
  .pitch-title { font-weight: 700; font-size: 15px; letter-spacing: .3px; }
  .pitch-list { list-style: none; margin: 4px 0 0 6px; }
  .pitch-list li {
    font-style: italic; font-size: 13px; line-height: 18px; padding-left: 16px; position: relative;
  }
  .pitch-list li::before {
    content: ""; position: absolute; left: 0; top: 6px;
    width: 7px; height: 7px; border-radius: 50%; background: var(--white);
  }
  .pitch-close { font-style: italic; font-size: 13px; margin-top: 6px; }
  .offer-title { font-weight: 700; font-size: 19px; margin-top: 10px; letter-spacing: .4px; }
  .offer-text { font-weight: 600; font-size: 13px; }

  /* Front side */
  .card-front {
    left: 620px;
    background: linear-gradient(160deg, var(--white) 55%, #f1f1f1 100%);
    color: var(--ink);
  }
  .logo {
    position: absolute; right: 30px; top: 36px;
    display: flex; align-items: center; gap: 10px;
  }
  .logo-dot { width: 30px; height: 30px; border-radius: 50%; background: var(--brand-green); }
  .logo-name {
    font-weight: 800; font-size: 28px; color: var(--ink); letter-spacing: 1px; line-height: 1;
  }
  .logo-tag {
    position: absolute; right: 30px; top: 76px;
    font-style: italic; font-size: 10px; color: var(--ink-soft);
  }
  .person { position: absolute; left: 40px; top: 118px; }
  .person-name { color: var(--brand-green); font-weight: 600; font-size: 20px; }
  .person-role { font-size: 15px; margin-top: 2px; }
  .contact { list-style: none; margin-top: 12px; }
  .contact li {
    display: flex; align-items: center; gap: 10px;
    font-size: 14px; color: var(--ink-soft); line-height: 24px;
  }
  .contact svg { width: 14px; height: 14px; fill: var(--brand-green); flex: none; }
</style>
</head>
<body>

  <section class="card card-back" aria-label="Card back">
    <div class="brand">
      <div class="brand-name">SUMMIT</div>
      <div class="brand-sub">MONEY COACHING</div>
      <div class="brand-tag">Achieve a new level of personal freedom</div>
    </div>
    <div class="pitch">
      <h2 class="pitch-title">STRUGGLING WITH YOUR FINANCES?</h2>
      <ul class="pitch-list">
        <li>Learn to become debt free</li>
        <li>Discover the power of cash</li>
        <li>Control your money instead of it controlling you</li>
      </ul>
      <p class="pitch-close">Let us help you achieve a new level of financial freedom!</p>
      <p class="offer-title">SPECIAL OFFER!</p>
      <p class="offer-text">FREE 30 minute consultation</p>
    </div>
  </section>

  <section class="card card-front" aria-label="Card front">
    <div class="logo">
      <span class="logo-dot"></span>
      <span class="logo-name">SUMMIT</span>
    </div>
    <div class="logo-tag">Summit Money Coaching · Achieve a new level of personal freedom</div>
    <div class="person">
      <h1 class="person-name">Daniel R. Hayes</h1>
      <p class="person-role">Personal Financial Coach</p>
      <ul class="contact">
        <li>
          <svg viewBox="0 0 14 14" aria-hidden="true"><rect x="3" y="0" width="8" height="14" rx="1.5"/><rect x="4.5" y="2" width="5" height="8" fill="#fff"/></svg>
          (205) 555-0142
        </li>
        <li>
          <svg viewBox="0 0 14 14" aria-hidden="true"><rect x="0" y="2" width="14" height="10" rx="1"/><path d="M1 3 L7 8 L13 3" stroke="#fff" stroke-width="1.3" fill="none"/></svg>
          daniel@steadyledgercoach.com
        </li>
        <li>
          <svg viewBox="0 0 14 14" aria-hidden="true"><circle cx="7" cy="7" r="7"/><path d="M0 7 H14 M7 0 C3 4 3 10 7 14 M7 0 C11 4 11 10 7 14" stroke="#fff" stroke-width="1" fill="none"/></svg>
          www.steadyledgercoach.com
        </li>
      </ul>
    </div>
  </section>

</body>
</html>
```